Slide Master for Holloway Engines - A Systematic Hedge Fund

We are looking for someone to produce a theme and slide master for us for our investor presentations. I have uploaded a few examples of templates that we would like to have included:
Main Title
Section Title
Slides with just bullet points
Different image/table configurations with bullet points and foot notes
Biographies of different lengths
A disclaimer (no one will read this but it should still look nice and needs to be in the presentations)
I have also uploaded the company logo, business card and colour definitions. Currently we have a blue colour scheme defined, but it would be nice to get a complementary set of colours so that when we have charts with more elements we can just draw from those.
The most important thing is that the slide master must be of general use to us. We arn't looking to have a specific presentation designed for us, but a theme/style that we can apply ourselves to any presentation we need to give in the future. It should have clearly defined guidelines for where content should go (and if this is different with and without footnotes for example). We would also like it to have a similar feel to the logo/business cards, so matt colours, high contrast, but not busy.
I'm excited to see the results!

```html
<!DOCTYPE html>
<html lang="en">
<head>
<meta charset="utf-8">
<title>Holloway Engines – Slide Master</title>
<link href="https://fonts.googleapis.com/css2?family=Montserrat:wght@500;600;700&family=Roboto:ital,wght@0,400;0,500;1,400&display=swap" rel="stylesheet">
<style>
:root{
  --stage:#3b3b3b;
  --navy:#0b3260;
  --slide:#123f76;
  --slide-deep:#0d3566;
  --accent:#3f7fd6;
  --accent-soft:#6e9fe6;
  --rule:#4a7bc4;
  --white:#ffffff;
  --text-soft:#d6e1f2;
}
*{margin:0;padding:0;box-sizing:border-box}
html,body{width:1200px;height:3839px;overflow:hidden;background:var(--stage)}
body{position:relative;font-family:'Roboto',sans-serif;color:var(--white)}
.slide{position:absolute;left:80px;width:1040px;height:585px;overflow:hidden}
.slide-bg{position:absolute;inset:0;background:linear-gradient(160deg,#164581 0%,var(--slide) 45%,var(--slide-deep) 100%)}
.top-rule{position:absolute;left:21px;top:46px;width:804px;height:5px;background:var(--accent)}
.corner-brand{position:absolute;right:28px;top:44px;width:170px;text-align:center;font-family:'Montserrat',sans-serif;font-weight:700;color:var(--white);line-height:1}
.corner-brand .line-one{display:block;font-size:21px;letter-spacing:.5px}
.corner-brand .line-two{display:block;margin-top:6px;font-size:11px;letter-spacing:8px}
.foot-rule{position:absolute;left:21px;right:28px;top:532px;height:1px;background:var(--rule)}
.footnote{position:absolute;left:24px;top:541px;font-size:8.5px;line-height:1.85;color:var(--text-soft);width:800px}

/* cover */
.cover{top:45px;background:var(--white)}
.cover-left{position:absolute;left:0;top:0;width:519px;height:100%;background:var(--navy)}
.cover-name{position:absolute;left:0;width:519px;top:270px;text-align:center;font-family:'Montserrat',sans-serif;font-weight:700;color:var(--white);line-height:1}
.cover-name .line-one{display:block;font-size:70px;letter-spacing:1px}
.cover-name .line-two{display:block;margin-top:22px;font-size:42px;letter-spacing:22px;padding-left:22px}
.cover-url{position:absolute;right:22px;top:220px;writing-mode:vertical-rl;font-size:10px;letter-spacing:2px;color:var(--navy);font-weight:500}
.social{position:absolute;display:flex;gap:7px}
.social span{width:19px;height:19px;border-radius:50%;background:var(--white)}
.cover .social{left:469px;top:509px}
.cover .social span:nth-child(n+3){background:var(--navy)}

/* section */
.section-title{position:absolute;left:0;right:0;text-align:center;font-family:'Montserrat',sans-serif;font-weight:600;font-size:50px;letter-spacing:.5px}
.section-sub{position:absolute;left:0;right:0;text-align:center;font-family:'Montserrat',sans-serif;font-weight:600;font-size:13px}

/* numbered grid */
.point{position:absolute;width:300px}
.point-num{position:absolute;left:0;top:-4px;font-family:'Montserrat',sans-serif;font-weight:700;font-size:56px;line-height:1}
.point h3{margin-left:53px;font-family:'Montserrat',sans-serif;font-weight:600;font-size:19px;letter-spacing:.3px}
.point p{margin-left:53px;margin-top:8px;font-size:10.5px;line-height:1.75;color:var(--text-soft)}

/* team */
.member{position:absolute;top:138px;width:220px;text-align:center}
.portrait-ring{width:166px;height:166px;margin:0 auto;border-radius:50%;border:1.5px solid var(--accent);padding:8px}
.portrait{width:100%;height:100%;border-radius:50%;background:radial-gradient(circle at 50% 40%,#c9c3bd 0%,#8d8580 55%,#3a3a3c 100%)}
.member h4{margin-top:22px;font-family:'Montserrat',sans-serif;font-weight:600;font-size:16px;letter-spacing:.5px}
.member .social{position:static;justify-content:center;gap:7px;margin-top:6px}
.member .social span{width:10px;height:10px;background:var(--accent-soft)}
.member p{margin-top:8px;font-style:italic;font-size:12px;line-height:2.2;color:var(--text-soft)}

/* closing */
.closing-name{position:absolute;left:40px;width:500px;top:282px;text-align:center;font-family:'Montserrat',sans-serif;font-weight:700;color:var(--white);line-height:1}
.closing-name .line-one{display:block;font-size:70px;letter-spacing:1px}
.closing-name .line-two{display:block;margin-top:20px;font-size:38px;letter-spacing:22px;padding-left:22px}
.thanks{position:absolute;left:628px;top:165px;width:360px}
.thanks h2{font-family:'Montserrat',sans-serif;font-weight:600;font-size:32px}
.thanks p{margin-top:10px;font-size:12px;line-height:1.85;color:var(--text-soft)}
.contact{list-style:none;margin-top:10px}
.contact li{display:flex;align-items:center;gap:12px;font-weight:500;font-size:13.5px;height:38px}
.contact svg{width:15px;height:15px;fill:var(--white)}
</style>
</head>
<body>

<section class="slide cover">
  <div class="cover-left"></div>
  <div class="cover-name"><span class="line-one">HOLLOWAY</span><span class="line-two">ENGINES</span></div>
  <div class="cover-url">WWW.HOLLOWAYENGINES.COM</div>
  <div class="social"><span></span><span></span><span></span><span></span></div>
</section>

<section class="slide" style="top:671px">
  <div class="slide-bg" role="img" aria-label="Faint photograph of a tall building under construction"></div>
  <div class="top-rule"></div>
  <div class="corner-brand"><span class="line-one">HOLLOWAY</span><span class="line-two">ENGINES</span></div>
  <h1 class="section-title" style="top:235px">LOREM IPSUM DOLOR SIT</h1>
  <div class="section-sub" style="top:318px">LOREM IPSUM DOLOR SIT AMET, CONSECTETUR ADIPISCING ELIT</div>
  <div class="foot-rule"></div>
  <p class="footnote">* Lorem ipsum dolor sit amet, consectetur adipiscing elit. Vestibulum lacinia eros eu pharetra mollis. Nullam vulputate purus mi, sed maximus<br>est sodales mollis. Mauris nec vulputate eros. Cras lectus lacus, lacinia eu dapibus ac, tincidunt eu nisi. Suspendisse in volutpat risus. Nunc pharetra porttitor lorem.</p>
</section>

<section class="slide" style="top:1297px">
  <div class="slide-bg" role="img" aria-label="Faint photograph of a tall building under construction"></div>
  <div class="top-rule"></div>
  <div class="corner-brand"><span class="line-one">HOLLOWAY</span><span class="line-two">ENGINES</span></div>
  <div class="point" style="left:30px;top:150px"><span class="point-num">1</span><h3>LOREM IPSUM</h3><p>Lorem ipsum dolor sit amet, consectetur adipiscing elit, sed do eiusmod tempor incididunt ut labore et dolore magna aliqua. Quis ipsum suspendisse ultrices gravida. Risus commodo viverra maecenas accumsan lacus vel facilisis.</p></div>
  <div class="point" style="left:370px;top:150px"><span class="point-num">2</span><h3>LOREM IPSUM</h3><p>Lorem ipsum dolor sit amet, consectetur adipiscing elit, sed do eiusmod tempor incididunt ut labore et dolore magna aliqua. Quis ipsum suspendisse ultrices gravida. Risus commodo viverra maecenas accumsan lacus vel facilisis.</p></div>
  <div class="point" style="left:710px;top:150px"><span class="point-num">3</span><h3>LOREM IPSUM</h3><p>Lorem ipsum dolor sit amet, consectetur adipiscing elit, sed do eiusmod tempor incididunt ut labore et dolore magna aliqua. Quis ipsum suspendisse ultrices gravida. Risus commodo viverra maecenas accumsan lacus vel facilisis.</p></div>
  <div class="point" style="left:30px;top:307px"><span class="point-num">4</span><h3>LOREM IPSUM</h3><p>Lorem ipsum dolor sit amet, consectetur adipiscing elit, sed do eiusmod tempor incididunt ut labore et dolore magna aliqua. Quis ipsum suspendisse ultrices gravida. Risus commodo viverra maecenas accumsan lacus vel facilisis.</p></div>
  <div class="point" style="left:370px;top:307px"><span class="point-num">5</span><h3>LOREM IPSUM</h3><p>Lorem ipsum dolor sit amet, consectetur adipiscing elit, sed do eiusmod tempor incididunt ut labore et dolore magna aliqua. Quis ipsum suspendisse ultrices gravida. Risus commodo viverra maecenas accumsan lacus vel facilisis.</p></div>
  <div class="point" style="left:710px;top:307px"><span class="point-num">6</span><h3>LOREM IPSUM</h3><p>Lorem ipsum dolor sit amet, consectetur adipiscing elit, sed do eiusmod tempor incididunt ut labore et dolore magna aliqua. Quis ipsum suspendisse ultrices gravida. Risus commodo viverra maecenas accumsan lacus vel facilisis.</p></div>
  <div class="foot-rule"></div>
  <p class="footnote">* Lorem ipsum dolor sit amet, consectetur adipiscing elit. Vestibulum lacinia eros eu pharetra mollis. Nullam vulputate purus mi, sed maximus<br>est sodales mollis. Mauris nec vulputate eros. Cras lectus lacus, lacinia eu dapibus ac, tincidunt eu nisi. Suspendisse in volutpat risus. Nunc pharetra porttitor lorem.</p>
</section>

<section class="slide" style="top:1923px">
  <div class="slide-bg" role="img" aria-label="Faint photograph of a tall building under construction"></div>
  <div class="top-rule"></div>
  <div class="corner-brand"><span class="line-one">HOLLOWAY</span><span class="line-two">ENGINES</span></div>
  <h1 class="section-title" style="top:235px">MEET OUR TEAM</h1>
  <div class="section-sub" style="top:318px">LOREM IPSUM DOLOR SIT AMET, CONSECTETUR ADIPISCING ELIT</div>
  <div class="foot-rule"></div>
  <p class="footnote">* Lorem ipsum dolor sit amet, consectetur adipiscing elit. Vestibulum lacinia eros eu pharetra mollis. Nullam vulputate purus mi, sed maximus<br>est sodales mollis. Mauris nec vulputate eros. Cras lectus lacus, lacinia eu dapibus ac, tincidunt eu nisi. Suspendisse in volutpat risus. Nunc pharetra porttitor lorem.</p>
</section>

<section class="slide" style="top:2548px">
  <div class="slide-bg" role="img" aria-label="Faint photograph of a tall building under construction"></div>
  <div class="top-rule"></div>
  <div class="corner-brand"><span class="line-one">HOLLOWAY</span><span class="line-two">ENGINES</span></div>
  <div class="member" style="left:73px"><div class="portrait-ring"><div class="portrait" role="img" aria-label="Portrait photo of a team member"></div></div><h4>JOHN DOE</h4><div class="social"><span></span><span></span><span></span><span></span></div><p>Lorem ipsum dolor sit amet, con-<br>sectetur adipiscing elit, sed do<br>eiusmod tempor</p></div>
  <div class="member" style="left:297px"><div class="portrait-ring"><div class="portrait" role="img" aria-label="Portrait photo of a team member"></div></div><h4>JOHN DOE</h4><div class="social"><span></span><span></span><span></span><span></span></div><p>Lorem ipsum dolor sit amet, con-<br>sectetur adipiscing elit, sed do<br>eiusmod tempor</p></div>
  <div class="member" style="left:521px"><div class="portrait-ring"><div class="portrait" role="img" aria-label="Portrait photo of a team member"></div></div><h4>JOHN DOE</h4><div class="social"><span></span><span></span><span></span><span></span></div><p>Lorem ipsum dolor sit amet, con-<br>sectetur adipiscing elit, sed do<br>eiusmod tempor</p></div>
  <div class="member" style="left:744px"><div class="portrait-ring"><div class="portrait" role="img" aria-label="Portrait photo of a team member"></div></div><h4>JOHN DOE</h4><div class="social"><span></span><span></span><span></span><span></span></div><p>Lorem ipsum dolor sit amet, con-<br>sectetur adipiscing elit, sed do<br>eiusmod tempor</p></div>
  <div class="foot-rule"></div>
  <p class="footnote">* Lorem ipsum dolor sit amet, consectetur adipiscing elit. Vestibulum lacinia eros eu pharetra mollis. Nullam vulputate purus mi, sed maximus<br>est sodales mollis. Mauris nec vulputate eros. Cras lectus lacus, lacinia eu dapibus ac, tincidunt eu nisi. Suspendisse in volutpat risus. Nunc pharetra porttitor lorem.</p>
</section>

<section class="slide" style="top:3174px">
  <div class="slide-bg" role="img" aria-label="Faint photograph of a tall building under construction"></div>
  <div class="top-rule"></div>
  <div class="closing-name"><span class="line-one">HOLLOWAY</span><span class="line-two">ENGINES</span></div>
  <div class="thanks">
    <h2>THANK YOU</h2>
    <p>Sed ut perspiciatis unde omnis iste natus error sit volup tatem accusantium doloremque laudantium, totam rem aperiam, eaque ipsa quae ab illo inventore veritatis et qu asi architecto beatae vitae dicta sunt expli</p>
    <ul class="contact">
      <li><svg viewBox="0 0 16 16"><path d="M3.5 1l3 3-1.6 2a9 9 0 0 0 5 5l2-1.6 3 3-1.8 2C7 14 2 9 1.5 2.8z"/></svg>+888 8888 8888</li>
      <li><svg viewBox="0 0 16 16"><path d="M8 1a7 7 0 1 0 0 14A7 7 0 0 0 8 1zm0 1.5c.7 0 1.5 1.5 1.8 4H6.2c.3-2.5 1.1-4 1.8-4zM2.6 6.5h2.1a14 14 0 0 0 0 3H2.6a5.6 5.6 0 0 1 0-3zm3.6 3h3.6c-.3 2.5-1.1 4-1.8 4s-1.5-1.5-1.8-4zm5.1 0a14 14 0 0 0 0-3h2.1a5.6 5.6 0 0 1 0 3z"/></svg>www.hollowayengines.com</li>
      <li><svg viewBox="0 0 16 16"><path d="M1 3h14v10H1zm1.5 1.5v.4L8 8.6l5.5-3.7v-.4z"/></svg>info@hollowayengines.com</li>
      <li><svg viewBox="0 0 16 16"><path d="M8 1a5 5 0 0 0-5 5c0 4 5 9 5 9s5-5 5-9a5 5 0 0 0-5-5zm0 7a2 2 0 1 1 0-4 2 2 0 0 1 0 4z"/></svg>123 Nenmo enim ipsam voluptatem quia</li>
    </ul>
  </div>
  <div class="foot-rule"></div>
  <p class="footnote">* Lorem ipsum dolor sit amet, consectetur adipiscing elit. Vestibulum lacinia eros eu pharetra mollis. Nullam vulputate purus mi, sed maximus<br>est sodales mollis. Mauris nec vulputate eros. Cras lectus lacus, lacinia eu dapibus ac, tincidunt eu nisi. Suspendisse in volutpat risus. Nunc pharetra porttitor lorem.</p>
</section>

</body>
</html>
```